Verpackungen für Shampoos
Zielgruppe
Wir sind ein kleines Familienunternehmen mit 2-3 Friseurfilialen und Onlineshop im Naturfriseurbereich, arbeiten mit ökologischen, nachhaltigen und natürlichen Produkten und vertreiben unsere eigene Haarbürste. Wir betreiben mit Sol Verde unsere eigene Marke in diesem Bereich. Erste Produkte, wie eine eigene Haarbürste sind bereits vorhanden und entstanden.
Für unsere erste Shampoo Serie suchen wir ein klares, cleanes und hochwertiges Design. Die 200ml Shampooflasche kommt komplett in weiß und besteh aus recyceltem Material. Es soll klar die ökologisch nachhaltige und etwas höherpreisige Marke kommuniziert werden. Dabei sehen wir vom Stil „weniger ist mehr“ als ganz klare Designvorgabe. Anbei auch ein Beispiel von Pavura, die das ganze sehr schön umgesetzt haben.
Die INCI sind noch nicht final. Es wäre schön, wenn hier ein Platzhalter eingefügt würde. Da eine der Hauptzielgruppen auch Österreicher sind, würden wir uns über ein kleines „Made in Austria“ auf der Vorderseite (evtl. ganz unten auf der Flasche) freuen.
Insgesamt sind es vier verschiedene Shampoos, die aus der gleichen Serie stammen. Es wäre schön, wenn man diese auch direkt unterscheiden könnte. Vielleicht durch ein grafisches Element, oder einfach nur durch die verschiedenen Namenserweiterungen. Hier die Aufstellung mit den Erweiterungen:
Es werden 4 verschiedene Shampoos, die Namen sind:
Change - Strapaziertes Haar
Care - Normales Haar
Sensitiv - Empfindliche Kopfhaut
Balancing - Fettiges Haar
Zielgruppe:
Weiblich, 30-60 Jahre, mittleres bis gehobenes Einkommen, nachhaltig, ökologisch, natürlich, legt Wert auf hochwertige Produkte und Dienstleistungen, achtet auf Konsum.
Aufgabenstellung
Die Landingpage zur Bürste ist hier erreichbar (Beispiel):
Vielleicht hilft das etwas um das Design und die Tonality aufzuschnappen: https://sol-verde.de/gold-birch-wildschweinborstenbuerste/
Es wäre super, wenn das Design der Flasche ähnlich klar und strukturiert ist.
Die Shampoos sind komplett vegan und made in Austria. Die beiden Aspekte sollten in Design auch aufgegriffen werden. Da wir einen 4 farbigen Tamponade/Siebdruck auf der Flasche anwenden, stehen leider nicht so viele Farben zur Verfügung (3-4).
Link zur Flasche:
https://www.brumoxa.com/de/kosmetik/varleno/varleno-tubica/flasche-heavy-200ml-24-410-plastik
Des Weiteren kann sich noch am Sol Verde Haarkonzept und unserem Dienstleistungsflyer orientiert werden.
Benefits:
-       Pflegt das Haar, hält es geschmeidig
- Bio Shampoo Konzentrat
-       Die Grundlage für gesunde Kopfhaut und schönes Haar*
-       Vermindert Spliss*
-       Hält die Haare natürlich geschmeidig
-       Regt die Durchblutung der Kopfhaut an
-       Verteilt Nährstoffe von der Wurzel bis in die Spitzen*
-       Verbessert das Kopfhautklima*
-       Für eine gut durchblutete und gesunde Kopfhaut mit glänzenden und
geschmeidigen Haaren*
-       Entfernt Schuppen und abgestorbene Hautpartikel
-       Verbessert natürlich die allgemeine Haarstruktur
-       Entwirrt langes und gelocktes Haar
-       Reinigt die Kopfhaut ohne Chemie*
-       Mehr Volumen im Haar
-       Mehr Stand im Haar durch Kräftigung der Haarbalkmuskulatur
-       Spart Shampoo und hilft Shampoo seltener und weniger zu nutzen
-       Nährstoffversorgung bis in die Haarspitzen
Inhaltsstoffe:
Care
Aloe Vera Direktsaft*, Decyl Glucoside, Coco Glucoside, Lauryl Glucoside, Hopfenextrakt*, Pentylene Glycol green, Meli..

```html
<!DOCTYPE html>
<html lang="de">
<head>
<meta charset="utf-8">
<title>Sol Verde Shampoo Serie</title>
<link rel="stylesheet" href="https://fonts.googleapis.com/css2?family=Cormorant+Garamond:wght@400;500&family=Josefin+Sans:ital,wght@0,300;0,400;1,300&family=Tenor+Sans&display=swap">
<style>
  :root {
    --canvas: #ffffff;
    --card: #ffffff;
    --bottle: #f7f7f7;
    --bottle-edge: #e6e6e6;
    --accent: #e0341f;
    --ink: #1e1e1e;
    --muted: #555555;
    --logo: #a3a3a3;
    --gold-dark: #a7843c;
    --gold-light: #f3dc9a;
    --cap-black: #050505;
  }
  * { box-sizing: border-box; margin: 0; padding: 0; }
  html, body { width: 1200px; height: 1196px; overflow: hidden; background: var(--canvas); }
  .series { position: relative; width: 1200px; height: 1196px; }
  .card {
    position: absolute; width: 563px; height: 563px; background: var(--card);
    box-shadow: 4px 5px 8px rgba(0,0,0,0.18);
  }
  .card--care { left: 614px; top: 23px; }
  .card--change { left: 23px; top: 23px; }
  .card--sensitiv { left: 23px; top: 609px; }
  .card--balancing { left: 614px; top: 609px; }

  .bottle { position: absolute; top: 47px; width: 156px; height: 480px; }
  .bottle--front { left: 63px; }
  .bottle--back { left: 347px; }
  .cap {
    position: absolute; left: 29px; top: 0; width: 98px; height: 62px;
    background: linear-gradient(90deg, var(--gold-dark) 0%, var(--gold-light) 22%, #c9a65a 28%, var(--cap-black) 28%, var(--cap-black) 72%, #c9a65a 72%, var(--gold-light) 82%, var(--gold-dark) 100%);
  }
  .body {
    position: absolute; left: 0; top: 62px; width: 156px; height: 418px;
    background: linear-gradient(90deg, var(--bottle-edge) 0%, var(--bottle) 8%, #ffffff 40%, var(--bottle) 90%, var(--bottle-edge) 100%);
    border-radius: 6px 6px 40px 40px / 4px 4px 10px 10px;
    box-shadow: 0 0 1px rgba(0,0,0,0.15);
  }

  .brand {
    position: absolute; left: 34px; top: 31px; display: flex; align-items: center; gap: 3px;
    font-family: "Cormorant Garamond", serif; font-size: 13px; color: var(--logo);
  }
  .brand-dot { width: 16px; height: 16px; border-radius: 50%; background: var(--logo); }
  .variant { position: absolute; left: 0; right: 0; top: 158px; text-align: center; color: var(--accent); font-family: "Tenor Sans", sans-serif; }
  .variant-name { font-size: 21px; line-height: 24px; }
  .variant-hair { font-family: "Cormorant Garamond", serif; font-size: 13px; line-height: 18px; }
  .product-type { position: absolute; left: 0; right: 0; top: 337px; text-align: center; font-family: "Cormorant Garamond", serif; font-size: 13px; color: var(--ink); }
  .claims { position: absolute; left: 0; right: 0; top: 357px; text-align: center; font-family: "Cormorant Garamond", serif; font-size: 8.5px; line-height: 12.5px; color: var(--ink); }

  .benefits { position: absolute; left: 14px; top: 59px; width: 140px; list-style: none; font-family: "Josefin Sans", sans-serif; font-weight: 300; font-size: 7.6px; line-height: 9.5px; color: var(--muted); }
  .benefits li { position: relative; padding-left: 8px; margin-bottom: 5.4px; }
  .benefits li::before { content: "✦"; position: absolute; left: 0; top: 0; color: var(--accent); font-size: 5px; }
  .ingredients { position: absolute; left: 17px; top: 241px; width: 128px; font-family: "Josefin Sans", sans-serif; font-weight: 300; font-size: 5.6px; line-height: 8px; color: var(--muted); }
  .ingredients-label { font-style: italic; }
  .vegan-mark { position: absolute; left: 62px; top: 352px; width: 30px; height: 30px; border-radius: 50%; background: #e2e2e2; border: 1px solid #cfcfcf; }
  .volume { position: absolute; left: 100px; top: 360px; font-family: "Josefin Sans", sans-serif; font-weight: 300; font-size: 13px; color: var(--accent); }
</style>
</head>
<body>
<main class="series">

  <section class="card card--change">
    <div class="bottle bottle--front">
      <div class="cap"></div>
      <div class="body">
        <div class="brand">Sol Verde <span class="brand-dot"></span></div>
        <div class="variant"><div class="variant-name">Cange</div><div class="variant-hair">strapaziertes Haar</div></div>
        <div class="product-type">Shampoo</div>
        <div class="claims">100 % vegan | 100 % natural<br>Made in Austria</div>
      </div>
    </div>
    <div class="bottle bottle--back">
      <div class="cap"></div>
      <div class="body">
        <ul class="benefits">
          <li>Bio Shampoo Konzentrat</li><li>Vermindert Spliss*</li><li>Verbessert das Kopfhautklima*</li><li>Mehr Volumen im Haar</li><li>Entfernt Schuppen und abgestor-<br>bene Hautpartikel</li><li>Entwirrt langes und gelocktes Haar</li><li>Reinigt die Kopfhaut ohne Chemie*</li><li>Nährstoffversorgung bis in die<br>Haarspitzen</li><li>Regt die Durchblutung der<br>Kopfhaut an</li>
        </ul>
        <p class="ingredients"><span class="ingredients-label">Inhaltsstoffe:</span><br>Aloe Vera Direktsaft*, Decyl Glucoside, Coco Glucoside, Lauryl Glucoside, Hopfenextrakt*, Pentylene Glycol green, Melissenblätter-Extrakt*, Arganöl*, Brokkolisamenöl*, Xanthan Gum, Parfümöl natürlich 'Maiglöckchen', Lorem ipsum dolor sit amet, consectetuer adipiscing elit, sed diam nonummy nibh euismod tincidunt ut laoreet dolore magna aliquam erat</p>
        <div class="vegan-mark"></div>
        <div class="volume">200 ml</div>
      </div>
    </div>
  </section>

  <section class="card card--care">
    <div class="bottle bottle--front">
      <div class="cap"></div>
      <div class="body">
        <div class="brand">Sol Verde <span class="brand-dot"></span></div>
        <div class="variant"><div class="variant-name">Care</div><div class="variant-hair">normales Haar</div></div>
        <div class="product-type">Shampoo</div>
        <div class="claims">100 % vegan | 100 % natural<br>Made in Austria</div>
      </div>
    </div>
    <div class="bottle bottle--back">
      <div class="cap"></div>
      <div class="body">
        <ul class="benefits">
          <li>Bio Shampoo Konzentrat</li><li>Vermindert Spliss*</li><li>Verbessert das Kopfhautklima*</li><li>Mehr Volumen im Haar</li><li>Entfernt Schuppen und abgestor-<br>bene Hautpartikel</li><li>Entwirrt langes und gelocktes Haar</li><li>Reinigt die Kopfhaut ohne Chemie*</li><li>Nährstoffversorgung bis in die<br>Haarspitzen</li><li>Regt die Durchblutung der<br>Kopfhaut an</li>
        </ul>
        <p class="ingredients"><span class="ingredients-label">Inhaltsstoffe:</span><br>Aloe Vera Direktsaft*, Decyl Glucoside, Coco Glucoside, Lauryl Glucoside, Hopfenextrakt*, Pentylene Glycol green, Melissenblätter-Extrakt*, Arganöl*, Brokkolisamenöl*, Xanthan Gum, Parfümöl natürlich 'Maiglöckchen', Lorem ipsum dolor sit amet, consectetuer adipiscing elit, sed diam nonummy nibh euismod tincidunt ut laoreet dolore magna aliquam erat</p>
        <div class="vegan-mark"></div>
        <div class="volume">200 ml</div>
      </div>
    </div>
  </section>

  <section class="card card--sensitiv">
    <div class="bottle bottle--front">
      <div class="cap"></div>
      <div class="body">
        <div class="brand">Sol Verde <span class="brand-dot"></span></div>
        <div class="variant"><div class="variant-name">Sensitiv</div><div class="variant-hair">empfindliche Kopfhaut</div></div>
        <div class="product-type">Shampoo</div>
        <div class="claims">100 % vegan | 100 % natural<br>Made in Austria</div>
      </div>
    </div>
    <div class="bottle bottle--back">
      <div class="cap"></div>
      <div class="body">
        <ul class="benefits">
          <li>Bio Shampoo Konzentrat</li><li>Vermindert Spliss*</li><li>Verbessert das Kopfhautklima*</li><li>Mehr Volumen im Haar</li><li>Entfernt Schuppen und abgestor-<br>bene Hautpartikel</li><li>Entwirrt langes und gelocktes Haar</li><li>Reinigt die Kopfhaut ohne Chemie*</li><li>Nährstoffversorgung bis in die<br>Haarspitzen</li><li>Regt die Durchblutung der<br>Kopfhaut an</li>
        </ul>
        <p class="ingredients"><span class="ingredients-label">Inhaltsstoffe:</span><br>Aloe Vera Direktsaft*, Decyl Glucoside, Coco Glucoside, Lauryl Glucoside, Hopfenextrakt*, Pentylene Glycol green, Melissenblätter-Extrakt*, Arganöl*, Brokkolisamenöl*, Xanthan Gum, Parfümöl natürlich 'Maiglöckchen', Lorem ipsum dolor sit amet, consectetuer adipiscing elit, sed diam nonummy nibh euismod tincidunt ut laoreet dolore magna aliquam erat</p>
        <div class="vegan-mark"></div>
        <div class="volume">200 ml</div>
      </div>
    </div>
  </section>

  <section class="card card--balancing">
    <div class="bottle bottle--front">
      <div class="cap"></div>
      <div class="body">
        <div class="brand">Sol Verde <span class="brand-dot"></span></div>
        <div class="variant"><div class="variant-name">Balancing</div><div class="variant-hair">fettiges Haar</div></div>
        <div class="product-type">Shampoo</div>
        <div class="claims">100 % vegan | 100 % natural<br>Made in Austria</div>
      </div>
    </div>
    <div class="bottle bottle--back">
      <div class="cap"></div>
      <div class="body">
        <ul class="benefits">
          <li>Bio Shampoo Konzentrat</li><li>Vermindert Spliss*</li><li>Verbessert das Kopfhautklima*</li><li>Mehr Volumen im Haar</li><li>Entfernt Schuppen und abgestor-<br>bene Hautpartikel</li><li>Entwirrt langes und gelocktes Haar</li><li>Reinigt die Kopfhaut ohne Chemie*</li><li>Nährstoffversorgung bis in die<br>Haarspitzen</li><li>Regt die Durchblutung der<br>Kopfhaut an</li>
        </ul>
        <p class="ingredients"><span class="ingredients-label">Inhaltsstoffe:</span><br>Aloe Vera Direktsaft*, Decyl Glucoside, Coco Glucoside, Lauryl Glucoside, Hopfenextrakt*, Pentylene Glycol green, Melissenblätter-Extrakt*, Arganöl*, Brokkolisamenöl*, Xanthan Gum, Parfümöl natürlich 'Maiglöckchen', Lorem ipsum dolor sit amet, consectetuer adipiscing elit, sed diam nonummy nibh euismod tincidunt ut laoreet dolore magna aliquam erat</p>
        <div class="vegan-mark"></div>
        <div class="volume">200 ml</div>
      </div>
    </div>
  </section>

</main>
</body>
</html>
```